Business Card for premium dental clinic

We are a premium dental clinic based in Brasov, Romania with more than 15 year on the market, providing quality dental treatment made by a team of more specialized dentists, working with modern equipment as a solution to beautiful and healthy teeth.

Our current logo for the clinic use 2 square with colors black and gold - dr Ternisu - studio, using family fonts Bodoni, Myriad Pro and Segoe Print.
Depending on the printing we used some gold CMYK background or gold foil picture background or a gold gradient.
We want a business card:
- eye catching business card
- distinguished business card
- premium design
- to keep the color scheme of black and gold
- to attract the customers to spent time reading the information
- modern concept

```html
<!DOCTYPE html>
<html lang="en">
<head>
<meta charset="utf-8">
<title>dr Ternisu studio – business card</title>
<link rel="stylesheet" href="https://fonts.googleapis.com/css2?family=Jost:wght@400;500&display=swap">
<style>
  :root {
    --ink: #231f20;
    --gold: #e9b423;
    --gold-light: #f7c844;
    --gold-deep: #c98a0c;
    --paper: #ffffff;
  }
  * { margin: 0; padding: 0; box-sizing: border-box; }
  html, body { width: 902px; height: 1200px; overflow: hidden; background: var(--paper); }
  body { position: relative; font-family: "Jost", sans-serif; }

  .card {
    position: absolute;
    left: 78px;
    width: 760px;
    height: 440px;
    border-radius: 20px;
    overflow: hidden;
    box-shadow: 3px 5px 8px rgba(0,0,0,0.28);
  }
  .card--front { top: 133px; }
  .card--back { top: 635px; }

  .gold-foil {
    position: absolute;
    inset: 0;
    background:
      radial-gradient(circle at 30% 25%, var(--gold-light) 0%, transparent 55%),
      radial-gradient(circle at 75% 80%, var(--gold-deep) 0%, transparent 60%),
      linear-gradient(135deg, var(--gold) 0%, #dba11a 50%, var(--gold) 100%);
  }

  .info-panel {
    position: absolute;
    left: 0; top: 0;
    width: 381px; height: 100%;
    background: var(--ink);
    color: var(--gold);
  }
  .info-panel__name {
    position: absolute;
    left: 51px; top: 94px;
    font-size: 29px;
    font-weight: 400;
    letter-spacing: 0.3px;
    line-height: 1;
  }
  .info-panel__role {
    position: absolute;
    left: 51px; top: 127px;
    font-size: 17px;
    line-height: 1;
  }
  .info-panel__rule {
    position: absolute;
    left: 51px; top: 155px;
    width: 130px; height: 1px;
    background: var(--gold);
  }
  .info-panel__address {
    position: absolute;
    left: 51px; top: 256px;
    font-size: 17px;
    line-height: 23px;
  }
  .contact-list {
    position: absolute;
    left: 51px; top: 347px;
    list-style: none;
    font-size: 17px;
    line-height: 23px;
  }
  .contact-list li { display: flex; align-items: center; }
  .contact-list svg { width: 12px; height: 12px; margin-right: 12px; fill: var(--gold); }

  .brand {
    position: absolute;
    display: flex;
    align-items: center;
    transform: translate(-50%, -50%);
  }
  .brand__square { background: var(--ink); flex: none; }
  .brand__name {
    color: var(--ink);
    font-weight: 500;
    white-space: nowrap;
    line-height: 1;
  }

  .card--front .brand { left: 570px; top: 234px; gap: 12px; }
  .card--front .brand__square { width: 26px; height: 26px; }
  .card--front .brand__name { font-size: 26px; }

  .card--back .brand { left: 380px; top: 225px; gap: 20px; }
  .card--back .brand__square { width: 48px; height: 48px; }
  .card--back .brand__name { font-size: 50px; }
</style>
</head>
<body>

<section class="card card--front">
  <div class="gold-foil" role="img" aria-label="Gold foil textured background"></div>
  <div class="info-panel">
    <h1 class="info-panel__name">DR. TERNISU</h1>
    <p class="info-panel__role">Dental specialist</p>
    <div class="info-panel__rule"></div>
    <p class="info-panel__address">12th floor, Morvan Road no<br>118 Tower Central</p>
    <ul class="contact-list">
      <li>
        <svg viewBox="0 0 12 12" aria-hidden="true"><path d="M2.5 0.5 L4.5 3 L3.3 4.4 Q4.5 7 7.6 8.7 L9 7.5 L11.5 9.5 L10 11.5 Q4.5 11 0.5 2 Z"/></svg>
        0219876543
      </li>
      <li>
        <svg viewBox="0 0 12 12" aria-hidden="true"><path d="M0.5 2.5 H11.5 V10 H0.5 Z M1.2 3.2 L6 6.8 L10.8 3.2" stroke="#231f20" stroke-width="0.8"/></svg>
        front.desk@brightsmile.co.nz
      </li>
      <li>
        <svg viewBox="0 0 12 12" aria-hidden="true"><circle cx="6" cy="6" r="5.5"/><path d="M3 3.5 Q5 4.5 4.5 6.5 Q6.5 7 6 9.5 M7.5 2 Q8 4 10 4.5" stroke="#231f20" stroke-width="1" fill="none"/></svg>
        www.brightsmile.co.nz
      </li>
    </ul>
  </div>
  <div class="brand">
    <span class="brand__square"></span>
    <span class="brand__name">dr Ternisu studio</span>
  </div>
</section>

<section class="card card--back">
  <div class="gold-foil" role="img" aria-label="Gold foil textured background"></div>
  <div class="brand">
    <span class="brand__square"></span>
    <span class="brand__name">dr Ternisu studio</span>
  </div>
</section>

</body>
</html>
```